WP website design (Tarnwick)

We need a wordpress design for an established auction and real estate company based in Arkansas. The winning design will incorporate a professional color scheme with company logo in a clean layout. The design needs to consider that this will be developed on a responsive theme.

Industry/Entity Type

Real Estate

Font styles to use
Sans Serif

Colors

Designer to choose colors to be used in the design.

Requirements
Must have
• Site will have slideshow, please use stock real estate or other image. A rough idea of homepage content is attached - not necessarily for design purposes.

Navigation Structure is:
1) Home
2) Auctions
3) Services
4) For Sale
5) About Us
6) Auction Videos
7) News & Events
8) Contact Us

Widgets will include:
Social media icons (Facebook, Youtube, RSS)
Testimonials Widget - this should be prominent
Featured Video
Email Signup form (Sign up to receive exclusive email updates for Tarnwick auctions. )
Nice to have
• A drop down menu example
Should not have
• no gavel in the design

```html
<!DOCTYPE html>
<html lang="en">
<head>
<meta charset="utf-8">
<title>Tarnwick Auction &amp; Marketing</title>
<link href="https://fonts.googleapis.com/css2?family=Open+Sans:wght@400;600;700;800&display=swap" rel="stylesheet">
<style>
:root{
  --green:#1f7a3a;
  --green-dark:#0f4a22;
  --green-deep:#0b3418;
  --panel:#154f27;
  --text:#444;
  --muted:#777;
  --line:#dcdcdc;
  --bg:#ffffff;
  --soft:#f3f3f3;
}
*{box-sizing:border-box;margin:0;padding:0}
html,body{width:833px;height:1200px;overflow:hidden;background:var(--bg);font-family:'Open Sans',Arial,sans-serif;color:var(--text)}
.page{width:833px;height:1200px;position:relative}
.wrap{width:733px;margin:0 auto;position:relative}

.site-header{height:42px}
.site-header .wrap{height:42px;display:flex;align-items:center;justify-content:space-between}
.brand{display:flex;align-items:center;gap:7px}
.brand-mark{width:16px;height:16px;border-radius:50%;background:var(--green)}
.brand-name{font-weight:800;font-size:18px;color:var(--green-dark);letter-spacing:1px;line-height:1}
.brand-sub{font-size:6.5px;color:var(--green-dark);font-weight:700;letter-spacing:.8px;display:block;margin-top:2px}
.header-right{display:flex;align-items:center;gap:10px;font-size:9px;color:var(--muted)}
.header-right strong{color:var(--green-dark)}
.search{width:110px;height:18px;border:1px solid var(--line);font-size:8px;color:#999;padding:3px 6px}

.main-nav{height:20px;background:var(--green)}
.main-nav ul{list-style:none;display:flex;height:20px}
.main-nav li{color:#fff;font-size:8.5px;font-weight:600;text-transform:uppercase;padding:0 14px;line-height:20px;border-right:1px solid rgba(255,255,255,.25);white-space:nowrap}
.main-nav li.active{background:var(--green-dark)}

.hero{height:300px;margin-top:5px;position:relative}
.hero-slide{position:absolute;left:0;top:0;width:733px;height:300px;background:linear-gradient(110deg,#3c2a1e 0%,#6b4a33 35%,#2a2320 70%,#14110f 100%)}
.slide-dots{position:absolute;left:20px;bottom:12px;display:flex;gap:5px}
.slide-dots span{width:7px;height:7px;border-radius:50%;background:rgba(255,255,255,.5)}
.slide-dots span:first-child{background:#fff}
.signup{position:absolute;right:0;top:0;width:168px;height:300px;background:var(--panel);padding:16px 14px;color:#fff}
.signup h2{font-size:11px;font-weight:400}
.signup h3{font-size:16px;font-weight:800;letter-spacing:1px;margin-bottom:12px}
.signup .field{height:20px;background:#fff;margin-bottom:8px;font-size:8px;color:#999;padding:4px 6px}
.signup .field.tall{height:48px}
.signup .btn{float:right;background:var(--green);border:1px solid #6fb383;font-size:8px;font-weight:700;padding:4px 10px;text-transform:uppercase}

.testimonials{height:150px;text-align:center;padding-top:16px}
.section-title{font-size:13px;font-weight:800;color:var(--green-dark);text-transform:uppercase;display:inline-block;border-bottom:1px solid var(--line);padding:0 40px 5px}
.quote{display:flex;gap:14px;align-items:flex-start;text-align:left;margin:14px 40px 0}
.quote-photo{width:62px;height:68px;flex:none;background:linear-gradient(#c9cfd6,#8e98a4)}
.quote-mark{font-size:38px;color:#ccc;line-height:.8;font-family:Georgia,serif}
.quote p{font-size:8.5px;line-height:1.5;color:var(--text)}
.quote p.lead{color:#333;font-weight:600;margin-bottom:4px}

.block-title{font-size:11px;font-weight:800;color:var(--green);text-transform:uppercase;border-bottom:1px solid var(--line);padding-bottom:4px;margin-bottom:10px}
.listing{display:flex;gap:12px;height:108px;padding-bottom:10px;margin-bottom:10px;border-bottom:1px solid var(--line)}
.listing-photo{width:142px;height:96px;flex:none}
.listing h4{font-size:10.5px;font-weight:700;color:var(--green-dark);margin-bottom:4px}
.listing p{font-size:7.5px;line-height:1.5;color:var(--muted);height:46px;overflow:hidden}
.listing-actions{display:flex;justify-content:space-between;align-items:center;margin-top:6px}
.btns{display:flex;gap:4px}
.btns span{background:var(--green);color:#fff;font-size:6.5px;font-weight:700;padding:3px 7px;text-transform:uppercase}
.share{display:flex;gap:4px}
.share span{width:22px;height:11px;background:#e4e4e4;border:1px solid #cfcfcf;border-radius:2px}

.video{display:flex;gap:14px;margin-top:4px}
.video-frame{width:200px;height:82px;flex:none;background:linear-gradient(135deg,#4b6a4f,#1d2d22);position:relative}
.video p{font-size:7.5px;line-height:1.55;color:var(--muted)}

.site-footer{position:absolute;left:0;bottom:0;width:833px;height:60px;background:var(--green-deep);color:#d8e6dc}
.site-footer .wrap{display:flex;justify-content:space-between;padding-top:12px}
.connect h5{font-size:8px;text-transform:uppercase;font-weight:700;margin-bottom:5px}
.socials{display:flex;gap:5px}
.socials span{width:16px;height:16px;border-radius:50%;background:#2f8a4b}
.footer-nav{text-align:right;font-size:7.5px}
.footer-nav p+p{margin-top:6px;color:#9fb8a6}
</style>
</head>
<body>
<div class="page">
  <header class="site-header">
    <div class="wrap">
      <div class="brand">
        <span class="brand-mark"></span>
        <div><span class="brand-name">TARNWICK</span><span class="brand-sub">AUCTION &amp; MARKETING, LLC</span></div>
      </div>
      <div class="header-right">
        <span>Call Us Today at <strong>800.555.0142</strong></span>
        <div class="search">Enter Keyword</div>
      </div>
    </div>
  </header>

  <nav class="main-nav">
    <div class="wrap">
      <ul>
        <li class="active">Home</li><li>Auctions</li><li>Services</li><li>For Sale</li><li>About Us</li><li>Auction Videos</li><li>News &amp; Events</li><li>Contact Us</li>
      </ul>
    </div>
  </nav>

  <section class="wrap hero">
    <div class="hero-slide" role="img" aria-label="Slideshow photo of a bidder raising a numbered auction paddle"></div>
    <div class="slide-dots"><span></span><span></span><span></span></div>
    <form class="signup">
      <h2>Welcome to</h2>
      <h3>TARNWICK</h3>
      <div class="field">Name</div>
      <div class="field">E-mail</div>
      <div class="field">Password</div>
      <div class="field tall">Message</div>
      <span class="btn">Sign Up</span>
    </form>
  </section>

  <section class="wrap testimonials">
    <h2 class="section-title">Testimonials</h2>
    <div class="quote">
      <div class="quote-photo" role="img" aria-label="Portrait of a satisfied client"></div>
      <span class="quote-mark">&ldquo;</span>
      <div>
        <p class="lead">Lorem Ipsum is simply dummy text of the printing and typesetting industry. Lorem Ipsum has been the industry's standard dummy text ever since the 1500s, when an unknown printer took a galley of type and scrambled it.</p>
        <p>Contrary to popular belief, Lorem Ipsum is not simply random text. It has roots in a piece of classical Latin literature from 45 BC, making it over 2000 years old. A professor at a college in Virginia looked up one of the more obscure Latin words and went through the cites of the word in classical literature.</p>
      </div>
    </div>
  </section>

  <section class="wrap auctions">
    <h3 class="block-title">Current Auctions</h3>
    <article class="listing">
      <div class="listing-photo" role="img" aria-label="Photo of a classic green sports car" style="background:linear-gradient(135deg,#6f8f6a,#254a2c)"></div>
      <div>
        <h4>Lorem Ipsum is simply dummy text of the printing and typesetting industry</h4>
        <p>Contrary to popular belief, Lorem Ipsum is not simply random text. It has roots in a piece of classical Latin literature from 45 BC, making it over 2000 years old. A professor at a college in Virginia looked up one of the more obscure Latin words, consectetur, from a Lorem Ipsum passage, and going through the cites.</p>
        <div class="listing-actions"><div class="btns"><span>Book Now</span><span>Photo Gallery</span><span>Details</span></div><div class="share"><span></span><span></span><span></span></div></div>
      </div>
    </article>
    <article class="listing">
      <div class="listing-photo" role="img" aria-label="Photo of a brick family house with a lawn" style="background:linear-gradient(160deg,#8fb3d6,#a58a6c 60%,#5d7a46)"></div>
      <div>
        <h4>Lorem Ipsum is simply dummy text of the printing and typesetting industry</h4>
        <p>Contrary to popular belief, Lorem Ipsum is not simply random text. It has roots in a piece of classical Latin literature from 45 BC, making it over 2000 years old. A professor at a college in Virginia looked up one of the more obscure Latin words, consectetur, from a Lorem Ipsum passage, and going through the cites.</p>
        <div class="listing-actions"><div class="btns"><span>Book Now</span><span>Photo Gallery</span><span>Details</span></div><div class="share"><span></span><span></span><span></span></div></div>
      </div>
    </article>
    <article class="listing">
      <div class="listing-photo" role="img" aria-label="Photo of a large suburban home" style="background:linear-gradient(160deg,#9dc0e0,#c9b08e 55%,#6f8a52)"></div>
      <div>
        <h4>Lorem Ipsum is simply dummy text of the printing and typesetting industry</h4>
        <p>Contrary to popular belief, Lorem Ipsum is not simply random text. It has roots in a piece of classical Latin literature from 45 BC, making it over 2000 years old. A professor at a college in Virginia looked up one of the more obscure Latin words, consectetur, from a Lorem Ipsum passage, and going through the cites.</p>
        <div class="listing-actions"><div class="btns"><span>Book Now</span><span>Photo Gallery</span><span>Details</span></div><div class="share"><span></span><span></span><span></span></div></div>
      </div>
    </article>
    <article class="listing">
      <div class="listing-photo" role="img" aria-label="Photo of a stone house with landscaped garden" style="background:linear-gradient(160deg,#b7cfe4,#b49a78 55%,#4f6e3c)"></div>
      <div>
        <h4>Lorem Ipsum is simply dummy text of the printing and typesetting industry</h4>
        <p>Contrary to popular belief, Lorem Ipsum is not simply random text. It has roots in a piece of classical Latin literature from 45 BC, making it over 2000 years old. A professor at a college in Virginia looked up one of the more obscure Latin words, consectetur, from a Lorem Ipsum passage, and going through the cites.</p>
        <div class="listing-actions"><div class="btns"><span>Book Now</span><span>Photo Gallery</span><span>Details</span></div><div class="share"><span></span><span></span><span></span></div></div>
      </div>
    </article>
  </section>

  <section class="wrap featured">
    <h3 class="block-title">Featured Video</h3>
    <div class="video">
      <div class="video-frame" role="img" aria-label="Featured auction video preview">
        <svg width="200" height="82" viewBox="0 0 200 82"><circle cx="100" cy="41" r="14" fill="rgba(255,255,255,.85)"/><path d="M95 33 L108 41 L95 49 Z" fill="#154f27"/></svg>
      </div>
      <p>Contrary to popular belief, Lorem Ipsum is not simply random text. It has roots in a piece of classical Latin literature from 45 BC, making it over 2000 years old. A professor at a college in Virginia looked up one of the more obscure Latin words, consectetur, from a Lorem Ipsum passage, and going through the cites of the word in classical literature, discovered the undoubtable source. It uses a dictionary of over 200 Latin words, combined with a handful of model sentence structures, to generate Lorem Ipsum which looks reasonable and free from repetition.</p>
    </div>
  </section>

  <footer class="site-footer">
    <div class="wrap">
      <div class="connect">
        <h5>Connect with us</h5>
        <div class="socials"><span></span><span></span><span></span></div>
      </div>
      <div class="footer-nav">
        <p>Home | Auctions | Services | For Sale | About Us | Auction Videos | News &amp; Events | Contact Us</p>
        <p>Copyright &copy; 2013 All Rights Reserved</p>
      </div>
    </div>
  </footer>
</div>
</body>
</html>
```